Verlindo Magician

I want the business card for my business to give to people who watch that later I will be employed to show magic here is my website http://www.verlindoillusions.example/I want the interesting design , i am very opened for formal and informal, I watch a lot of design so don't stick to the common shape and form but i hope it can also be produced the thing to write on will be the same as in picture that i will upload , i also will upload the logo for you that so can be easy to useDenis CostilleMagicianMAGICIAN BALSAMO 17 rue des Tilleuls - 25000 BESANÇON contact@verlindoillusions.example tel. 0381 946 157 tel. 0674 219 503

```html
<!DOCTYPE html>
<html lang="fr">
<head>
<meta charset="utf-8">
<title>Verlindo Magician – Business Card</title>
<link href="https://fonts.googleapis.com/css2?family=Montserrat:wght@400;500;700&family=Questrial&display=swap" rel="stylesheet">
<style>
  :root {
    --stage: #e4e4e4;
    --card-black: #151515;
    --card-white: #ffffff;
    --ink: #111111;
    --accent: #e2372b;
    --rule: #1a1a1a;
    --figure-dark: #1c1c1c;
    --figure-light: #d8d8d8;
  }
  * { margin: 0; padding: 0; box-sizing: border-box; }
  html, body { width: 1200px; height: 895px; overflow: hidden; }
  body {
    background: var(--stage);
    font-family: "Montserrat", sans-serif;
    color: var(--ink);
    position: relative;
  }
  .card {
    position: absolute;
    left: 320px;
    width: 560px;
    height: 320px;
    box-shadow: 0 6px 18px rgba(0,0,0,.18);
  }
  .card--back { top: 97px; background: var(--card-black); }
  .card--front { top: 477px; background: var(--card-white); }

  /* brand block */
  .brand { position: absolute; text-align: center; }
  .brand__figure { margin: 0 auto; border-radius: 40% 40% 6px 6px; }
  .brand__name {
    font-family: "Questrial", sans-serif;
    font-weight: 400;
    letter-spacing: .08em;
    line-height: 1;
    display: block;
  }
  .brand__tag {
    font-family: "Questrial", sans-serif;
    font-weight: 400;
    letter-spacing: .18em;
    display: block;
    margin-top: 4px;
  }

  .card--back .brand { right: 48px; top: 92px; width: 180px; color: #ffffff; }
  .card--back .brand__figure {
    width: 80px; height: 70px;
    background: linear-gradient(180deg, var(--figure-light), #f4f4f4);
  }
  .card--back .brand__name { font-size: 30px; margin-top: 10px; }
  .card--back .brand__tag { font-size: 9px; }

  .card--front .brand { left: 40px; top: 46px; width: 200px; color: var(--ink); }
  .card--front .brand__figure {
    width: 150px; height: 150px;
    background: linear-gradient(180deg, #3a3a3a, var(--figure-dark));
  }
  .card--front .brand__name { font-size: 30px; margin-top: 12px; }
  .card--front .brand__tag { font-size: 9px; }

  .divider {
    position: absolute;
    left: 262px; top: 78px;
    width: 1px; height: 190px;
    background: var(--rule);
  }

  .contact { position: absolute; left: 290px; top: 58px; }
  .contact__name {
    font-size: 22px; font-weight: 700;
    letter-spacing: .01em; text-transform: uppercase;
    line-height: 1.05;
  }
  .contact__role {
    font-size: 13px; font-weight: 400; color: var(--accent);
    letter-spacing: .04em; margin: 2px 0 0 12px;
  }
  .contact__list { list-style: none; margin: 12px 0 0 30px; font-size: 12.5px; line-height: 1.5; }
  .contact__address { margin-bottom: 4px; }
  .contact__item { display: flex; align-items: center; gap: 8px; white-space: nowrap; }
  .contact__item svg { width: 11px; height: 11px; flex: none; fill: var(--accent); }
</style>
</head>
<body>

  <section class="card card--back">
    <div class="brand">
      <div class="brand__figure" role="img" aria-label="Illustration of the magician holding a playing card"></div>
      <span class="brand__name">VERLINDO</span>
      <span class="brand__tag">MAGICIAN</span>
    </div>
  </section>

  <section class="card card--front">
    <div class="brand">
      <div class="brand__figure" role="img" aria-label="Illustration of the magician holding a playing card"></div>
      <span class="brand__name">VERLINDO</span>
      <span class="brand__tag">MAGICIAN</span>
    </div>

    <div class="divider"></div>

    <div class="contact">
      <h1 class="contact__name">Marc Ravoulet</h1>
      <p class="contact__role">MAGICIAN</p>
      <ul class="contact__list">
        <li class="contact__address">17 rue des Tilleuls<br>25000 BESANÇON</li>
        <li class="contact__item">
          <svg viewBox="0 0 24 24"><path d="M6.6 10.8a15.1 15.1 0 0 0 6.6 6.6l2.2-2.2c.3-.3.7-.4 1-.2 1.1.4 2.3.6 3.6.6.6 0 1 .4 1 1V20c0 .6-.4 1-1 1A17 17 0 0 1 3 4c0-.6.4-1 1-1h3.5c.6 0 1 .4 1 1 0 1.3.2 2.5.6 3.6.1.3 0 .7-.2 1z"/></svg>
          0381 946 157
        </li>
        <li class="contact__item">
          <svg viewBox="0 0 24 24"><path d="M6.6 10.8a15.1 15.1 0 0 0 6.6 6.6l2.2-2.2c.3-.3.7-.4 1-.2 1.1.4 2.3.6 3.6.6.6 0 1 .4 1 1V20c0 .6-.4 1-1 1A17 17 0 0 1 3 4c0-.6.4-1 1-1h3.5c.6 0 1 .4 1 1 0 1.3.2 2.5.6 3.6.1.3 0 .7-.2 1z"/></svg>
          0674 219 503
        </li>
        <li class="contact__item">
          <svg viewBox="0 0 24 24"><path d="M2 5h20v14H2zm2 2v.5l8 5 8-5V7l-8 5z"/></svg>
          contact@verlindoillusions.example
        </li>
        <li class="contact__item">
          <svg viewBox="0 0 24 24"><path d="M12 2a10 10 0 1 0 0 20 10 10 0 0 0 0-20zm6.9 9h-3a15 15 0 0 0-1.2-5.5A8 8 0 0 1 18.9 11zM12 4c.9 1.2 1.8 3.6 1.9 7h-3.8c.1-3.4 1-5.8 1.9-7zM9.3 5.5A15 15 0 0 0 8.1 11h-3a8 8 0 0 1 4.2-5.5zM5.1 13h3a15 15 0 0 0 1.2 5.5A8 8 0 0 1 5.1 13zm6.9 7c-.9-1.2-1.8-3.6-1.9-7h3.8c-.1 3.4-1 5.8-1.9 7zm2.7-1.5a15 15 0 0 0 1.2-5.5h3a8 8 0 0 1-4.2 5.5z"/></svg>
          verlindoillusions.example
        </li>
      </ul>
    </div>
  </section>

</body>
</html>
```